Business Card Design for Vintage Jazz

I am a vintage jazz band leader in New York City. My groups play the music of the 1920s, 1930s and 1940s. My website is morvalquist.com for more info on what I do.

I am looking for a two sided business card design that has the look and feel of a really nice business card from the 1930s. I need to convey with the design that my work has that vintage kind of class and style, but also conveys that we are fun and entertaining.

Most importantly it should make a bold staement. If Hal Denbrook had a card, what would it have looked like? I want a card that I feel confident will make an impact and will let people know that my work is te the top that NYC has to offer in vintage jazz..

Note that I have only decided to avoid the "committed payment" option as I have not used this service before. Assuming that I get quality work I will select a design from those presented.

Target Market(s)

people who want to hire my band for events, media, and new fans of the band

Industry/Entity Type

Performing Art

Contact Information for Business Card

Definitely a matte finish, possibly a sort of old style of paper with that brown tint? definitely a thick card.

Requirements
Must have
• FRONT
• My name: Tobin Vashley
• What I do: Bandleader, Guitarist, Vocalist, Songwriter
• Contact Details: morvalquist.com tobin@morvalquist.com 646-555-0148
• BACK
• My Social Media Links:
• facebook.morvalquist.com
• twitter, instagram, linkedin: morvalquist
• I'm also including a photo image I would like to use. The photo's background is not needed, and to be honest isn't really desireable. Just looking to use the image of me.
Nice to have
• I'm attaching which could be used as is, omitted from the card, or altered maybe with text going around the outside of the circle or in some other way. It may need some clean up to the edges of the lettering as we only use it for the website thumbnail.
• If there's space I'd like to include the text "join our mailing list for a free song download: freesong.morvalquist.com" If not perhaps just "Download a Free Song at: freesong.morvalquist.com - something to this end.
Should not have
• anything cartoony. Don't think retro 90s's vision of the swing era, think actual swing era!
• anything modern. Got to look old school
• Try to avoid dark backgrounds. Since we often play in bars and clubs where it is dar, a d
• avoid script fonts.

```html
<!DOCTYPE html>
<html lang="en">
<head>
<meta charset="utf-8">
<title>Tobin Vashley — Business Card</title>
<link rel="stylesheet" href="https://fonts.googleapis.com/css2?family=Source+Sans+3:wght@400;600&display=swap">
<style>
  :root {
    --canvas: #e8e4dd;
    --paper: #f3ece0;
    --paper-edge: #e6dccb;
    --ink-dark: #2a2622;
    --ink-light: #f8f3ea;
    --photo-tone-a: #a7a29b;
    --photo-tone-b: #3b3733;
    --font-main: "Source Sans 3", "Myriad Pro", Arial, sans-serif;
  }
  * { margin: 0; padding: 0; box-sizing: border-box; }
  html, body {
    width: 1200px; height: 900px; overflow: hidden;
    background: var(--canvas);
    font-family: var(--font-main);
  }
  .stage { position: relative; width: 1200px; height: 900px; }

  .card {
    position: absolute;
    overflow: hidden;
    background: linear-gradient(180deg, var(--paper) 0%, var(--paper-edge) 100%);
    box-shadow: 0 6px 18px rgba(60,45,30,0.18);
  }
  .card--front { left: 238px; top: 60px; width: 555px; height: 345px; }
  .card--back  { left: 457px; top: 518px; width: 560px; height: 342px; }

  .band { position: absolute; background: var(--ink-dark); }
  .card--front .band { left: 202px; top: 167px; right: 0; bottom: 0; }
  .card--back .band  { left: 0; top: 167px; right: 0; bottom: 0; }

  .portrait-photo {
    position: absolute; left: 0; top: 0; width: 236px; height: 345px;
    background: linear-gradient(160deg, var(--photo-tone-a) 0%, var(--photo-tone-b) 72%);
    border-radius: 0 60px 0 0;
    box-shadow: 3px 0 0 var(--ink-light);
  }
  .portrait-silhouette {
    position: absolute; left: 368px; top: 0; width: 192px; height: 170px;
    background: var(--ink-dark);
    border-radius: 90px 0 0 0;
  }

  .wordmark {
    position: absolute;
    font-weight: 600;
    letter-spacing: 0.08em;
    text-transform: uppercase;
    white-space: nowrap;
  }
  .card--front .wordmark { left: 262px; top: 68px; font-size: 24px; color: var(--ink-dark); }
  .card--back .wordmark  { left: 398px; top: 196px; font-size: 17px; color: var(--ink-light); }

  .contact-name {
    position: absolute; left: 280px; top: 207px;
    color: var(--ink-light); font-weight: 600; font-size: 19px;
  }
  .contact-list {
    position: absolute; left: 280px; top: 245px;
    list-style: none; color: var(--ink-light); font-size: 15px; line-height: 20px;
  }
  .contact-list li { display: flex; align-items: center; gap: 8px; }
  .contact-list svg { width: 11px; height: 11px; fill: var(--ink-light); }

  .social {
    position: absolute; left: 0; top: 238px; width: 390px;
    color: var(--ink-light); font-size: 15px; line-height: 25px;
  }
  .social-row { display: flex; align-items: center; }
  .social-left { width: 225px; text-align: right; }
  .social-mark {
    display: inline-block; width: 12px; height: 12px; background: var(--ink-light);
    margin-left: 11px; border-radius: 2px;
  }
  .social-mark + .social-mark { margin-left: 22px; }
  .social-right { margin-left: 12px; }

  .tagline {
    position: absolute; left: 97px; top: 300px;
    color: var(--ink-light); font-size: 15px; white-space: nowrap;
  }
</style>
</head>
<body>
<main class="stage">

  <section class="card card--front" aria-label="Card front">
    <div class="band"></div>
    <div class="portrait-photo" role="img" aria-label="Cut-out photo of the bandleader in a dark jacket with white piping and a neck scarf"></div>
    <div class="wordmark">Morvalquist</div>
    <h1 class="contact-name">Tobin Vashley</h1>
    <ul class="contact-list">
      <li><svg viewBox="0 0 12 12" aria-hidden="true"><path d="M2.5 0.5 L4.5 0.5 L5 3.2 L3.7 4.2 Q4.8 6.8 7.8 8.3 L8.8 7 L11.5 7.5 L11.5 9.5 Q11.5 11.5 9.5 11.5 Q0.5 10.5 0.5 2.5 Q0.5 0.5 2.5 0.5 Z"/></svg>646-555-0148</li>
      <li><svg viewBox="0 0 12 12" aria-hidden="true"><path d="M0.5 2 H11.5 V10 H0.5 Z"/><path d="M1 2.5 L6 6.5 L11 2.5" stroke="#2a2622" stroke-width="0.9" fill="none"/></svg>tobin@morvalquist.com</li>
      <li><svg viewBox="0 0 12 12" aria-hidden="true"><circle cx="6" cy="6" r="5.5"/><path d="M3 4 Q5 5 4.5 7 Q6.5 8 6 10.5 M8 2 Q7 4 9 5" stroke="#2a2622" stroke-width="1" fill="none"/></svg>morvalquist.com</li>
    </ul>
  </section>

  <section class="card card--back" aria-label="Card back">
    <div class="band"></div>
    <div class="portrait-silhouette" role="img" aria-label="Dark silhouette of the bandleader tipping his hat"></div>
    <div class="wordmark">Morvalquist</div>
    <div class="social">
      <div class="social-row">
        <span class="social-left">morvalquist.com</span>
        <span class="social-mark" aria-hidden="true"></span><span class="social-mark" aria-hidden="true"></span>
        <span class="social-right">morvalquist</span>
      </div>
      <div class="social-row">
        <span class="social-left">morvalquist</span>
        <span class="social-mark" aria-hidden="true"></span><span class="social-mark" aria-hidden="true"></span>
        <span class="social-right">morvalquist</span>
      </div>
    </div>
    <p class="tagline">Bandleader, Guitarist, Vocalist, Songwriter</p>
  </section>

</main>
</body>
</html>
```